Redesign of business card for Cedar Ridge Mechanical

We are looking for a new design for our business cards for Cedar Ridge Mechanical. We are a plumbing & HVAC construction company, operating on the West Coast of Canada and USA. Logo attached.
Industry/Entity Type
Construction - Plumbing & HVAC
Contact Information for Business Card
Name, address, phone numbers, email, website address
Look and feel
Each slider illustrates characteristics of the customer's brand and the style your logo design should communicate.

```html
<!DOCTYPE html>
<html lang="en">
<head>
<meta charset="utf-8">
<title>Cedar Ridge Mechanical – Business Card</title>
<link href="https://fonts.googleapis.com/css2?family=Montserrat:wght@400;700&family=Oswald:wght@600&display=swap" rel="stylesheet">
<style>
  :root {
    --stage: #1c1c1c;
    --card-black: #141414;
    --card-white: #f7f7f7;
    --swoosh-grey: #9a9a9a;
    --ink: #1a1a1a;
    --muted: #7a7a7a;
    --logo-white: #ffffff;
  }
  html, body {
    margin: 0;
    width: 1200px;
    height: 963px;
    overflow: hidden;
    background: var(--stage);
  }
  .card {
    position: absolute;
    left: 250px;
    width: 700px;
    height: 400px;
    border-radius: 26px;
    overflow: hidden;
    background: var(--card-black);
    box-shadow: 0 10px 30px rgba(0,0,0,.5);
  }
  .card--front { top: 60px; }
  .card--back { top: 503px; }
  .card__shape { position: absolute; inset: 0; }

  .wordmark {
    position: absolute;
    display: flex;
    align-items: center;
    gap: 14px;
    font-family: 'Oswald', sans-serif;
    font-weight: 600;
    color: var(--logo-white);
    text-transform: uppercase;
    letter-spacing: 2px;
    white-space: nowrap;
  }
  .wordmark__square { background: var(--logo-white); flex: none; }
  .card--front .wordmark { top: 68px; left: 250px; font-size: 30px; }
  .card--front .wordmark__square { width: 22px; height: 22px; }
  .card--back .wordmark { top: 168px; left: 0; right: 0; justify-content: center; font-size: 42px; }
  .card--back .wordmark__square { width: 30px; height: 30px; }

  .person {
    position: absolute;
    left: 40px;
    top: 232px;
    font-family: 'Montserrat', sans-serif;
  }
  .person__name { margin: 0; font-size: 24px; font-weight: 700; color: var(--ink); text-transform: uppercase; letter-spacing: .5px; }
  .person__surname { color: var(--muted); }
  .person__role { margin: 4px 0 0; font-size: 15px; color: var(--muted); text-align: right; }
  .address {
    position: absolute;
    left: 40px;
    top: 330px;
    margin: 0;
    font-family: 'Montserrat', sans-serif;
    font-size: 15px;
    color: var(--muted);
  }
  .divider {
    position: absolute;
    left: 330px;
    top: 272px;
    width: 1px;
    height: 48px;
    background: var(--muted);
  }
  .contact {
    position: absolute;
    left: 345px;
    top: 272px;
    margin: 0;
    padding: 0;
    list-style: none;
    font-family: 'Montserrat', sans-serif;
    font-size: 15px;
    color: var(--muted);
  }
  .contact li { display: flex; align-items: center; gap: 8px; height: 22px; white-space: nowrap; }
  .contact svg { width: 13px; height: 13px; fill: var(--ink); flex: none; }
  .contact strong { color: var(--ink); font-weight: 400; }
</style>
</head>
<body>

<section class="card card--front" aria-label="Business card front">
  <svg class="card__shape" viewBox="0 0 700 400" aria-hidden="true">
    <path d="M0,132 Q350,150 700,265 L700,400 L0,400 Z" fill="var(--swoosh-grey)"/>
    <path d="M0,126 Q340,140 620,230" fill="none" stroke="var(--card-white)" stroke-width="2"/>
    <path d="M0,148 Q360,168 700,292 L700,400 L0,400 Z" fill="var(--card-white)"/>
  </svg>

  <div class="wordmark"><span class="wordmark__square"></span>Cedar Ridge Mechanical</div>

  <div class="person">
    <p class="person__name">Daniel <span class="person__surname">Brooks</span></p>
    <p class="person__role">Manager</p>
  </div>
  <p class="address">Your address, city, state, ZIP 0000</p>

  <div class="divider"></div>
  <ul class="contact">
    <li><svg viewBox="0 0 24 24"><path d="M6.6 10.8a15 15 0 0 0 6.6 6.6l2.2-2.2a1 1 0 0 1 1-.25 11.4 11.4 0 0 0 3.6.57 1 1 0 0 1 1 1V20a1 1 0 0 1-1 1A17 17 0 0 1 3 4a1 1 0 0 1 1-1h3.5a1 1 0 0 1 1 1c0 1.25.2 2.45.57 3.57a1 1 0 0 1-.25 1z"/></svg><span>604-555-0182</span></li>
    <li><svg viewBox="0 0 24 24"><path d="M2 5h20v14H2zm2 2v.5l8 5 8-5V7l-8 5z"/></svg><span>daniel@cedarridgemech.com</span></li>
    <li><svg viewBox="0 0 24 24"><circle cx="12" cy="12" r="10"/></svg><span>www.<strong>cedarridgemech</strong>.com</span></li>
  </ul>
</section>

<section class="card card--back" aria-label="Business card back">
  <div class="wordmark"><span class="wordmark__square"></span>Cedar Ridge Mechanical</div>
</section>

</body>
</html>
```